Indy Film Production Company/Studio

We need a business card designed from an existing logo. We are a digital studio/production company that caters to creating genre entertainment, like Action, Horror, and martial arts. The card along with the logo will be used to Brand the company from letter heads to banners. The design will also be used for postcards and Brochures. It should be professional and masculine.
Updates

Thank you to all the designers who have participated. I'm narrowing down who it will be. Thank you again.

Target Market(s)

Investors, Networks, Producers, and actors

Industry/Entity Type

Film Production

Contact Information for Business Card

Teodoro Valbuena
Producer/Writer/Director
www.kestrelpicturehouse.example

Requirements
Must have
• Website address, Facebook icon and Twitter icon possibly in the back of the card.
Nice to have
• Logline of Company: Follow The Action.

```html
<!DOCTYPE html>
<html lang="en">
<head>
<meta charset="utf-8">
<title>Kestrel Picturehouse – Business Card</title>
<link rel="stylesheet" href="https://fonts.googleapis.com/css2?family=Source+Sans+3:wght@400;600;700&display=swap">
<style>
  :root {
    --stage: #2b2624;
    --card: #0d0d0d;
    --red: #e3232b;
    --white: #f2f2f2;
    --grey-light: #8a8a8a;
    --grey-dark: #1c1c1c;
  }
  * { box-sizing: border-box; margin: 0; padding: 0; }
  html, body {
    width: 1200px; height: 814px; overflow: hidden;
    background: var(--stage);
    font-family: "Source Sans 3", "Myriad Pro", sans-serif;
  }
  .card {
    position: absolute;
    width: 520px; height: 297px;
    background: var(--card);
    box-shadow: 0 10px 30px rgba(0,0,0,.45);
    overflow: hidden;
  }
  /* Front: contact side */
  .card--contact { left: 50px; top: 258px; }
  .viewfinder { position: absolute; inset: 0; }
  .contact {
    position: absolute; inset: 0;
    display: flex; flex-direction: column; align-items: center; justify-content: center;
    text-align: center; color: var(--white);
    font-size: 15px; line-height: 1.25;
  }
  .contact__mark {
    width: 22px; height: 22px; border-radius: 50%;
    background: var(--red); margin-bottom: 6px;
  }
  .contact__name { color: var(--red); font-size: 19px; font-weight: 600; }
  .contact__role { font-size: 15px; margin-bottom: 12px; }

  /* Back: brand side */
  .card--brand { left: 630px; top: 258px; }
  .hero-photo {
    position: absolute; left: 0; top: 0; width: 300px; height: 297px;
    background: radial-gradient(ellipse at 55% 45%, #6e6e6e 0%, #3a3a3a 38%, #151515 70%, var(--card) 100%);
  }
  .social-square {
    position: absolute; right: 16px; top: 14px;
    width: 18px; height: 18px; background: var(--red);
  }
  .brand {
    position: absolute; left: 300px; right: 16px; top: 110px;
    text-align: center;
  }
  .brand__name {
    color: var(--red); font-weight: 700; font-size: 27px;
    line-height: 1.05; text-transform: uppercase; letter-spacing: .02em;
  }
  .brand__web {
    color: var(--white); font-size: 11.5px; margin-top: 8px;
  }
</style>
</head>
<body>
  <section class="card card--contact" aria-label="Business card, contact side">
    <svg class="viewfinder" viewBox="0 0 520 297" aria-hidden="true">
      <g fill="none" stroke="var(--red)" stroke-width="3">
        <path d="M24 60 V26 H58"/>
        <path d="M462 26 H496 V60"/>
        <path d="M24 237 V271 H58"/>
        <path d="M462 271 H496 V237"/>
      </g>
    </svg>
    <div class="contact">
      <div class="contact__mark"></div>
      <p class="contact__name">Teodoro Valbuena</p>
      <p class="contact__role">Producer/Writer/Director</p>
      <p class="contact__phone">555 014 2290</p>
      <p class="contact__email">hello@kestrelpicturehouse.example</p>
      <p class="contact__web">www.kestrelpicturehouse.example</p>
    </div>
  </section>

  <section class="card card--brand" aria-label="Business card, brand side">
    <div class="hero-photo" role="img" aria-label="Photograph of a professional cinema camera rig on a tripod head"></div>
    <div class="social-square"></div>
    <div class="brand">
      <p class="brand__name">Kestrel<br>Picturehouse</p>
      <p class="brand__web">www.kestrelpicturehouse.example</p>
    </div>
  </section>
</body>
</html>
```